Web landing page design

- Create a Web Design (Uncoded - PSD layout only)

We need a single web page design to promote our service. This page will
acts as a landing page for users and also be utilized in social media
advertising. Please provide us with a cutting edge design. I have attached
a link for what the company is about. In essence we are a photo checking
service which reviews photos for retailers, hotels abd car dealerships to
check everything is good after a service has been performed. Whether it be
a new promotion, cleaning or just checking prices. I am looking for a
design to say that we do many photos and at a very cost effective price
(team based in Mexico)

Link: https://slidevault.example/view/qTr8nWx2LpZk4mHcYdJs/
*Deadline*
5 days
*Updates*

- The Start Here box needs to look like this:

-Start Here (heading)
-A box for email addresses to be entered
-Then a check box with "Yes, I have read and agree to the Privacy Policy
and agree to receive email marketing from Plumora88'
-A submit button

All of this information needs to be in one box please. And please feel
free to contact me if you have any questions about this.

*Target Market(s)*
Retail business, Merchandising companies, Rental property owners, Car
dealers
Updates

Please can you submit entries. I am just looking for a tidy to a presentation already created. Just needs design touches.

Target Market(s)

Ability for audience to understand concept quickly
Benefits to why to use the product stand out
Technology driven approach

Industry/Entity Type

Retail

Number of Pages Required

1 page

Colors
0792cd

Requirements
Must have
• Clean and modern design

```html
<!DOCTYPE html>
<html lang="en">
<head>
<meta charset="utf-8">
<title>Plumora88 – Start Here</title>
<link href="https://fonts.googleapis.com/css2?family=Lato:wght@300;400;700&display=swap" rel="stylesheet">
<style>
:root{
  --brand:#0792cd;
  --brand-dark:#0574a6;
  --brand-light:#2fb0e6;
  --ink:#2b2f33;
  --muted:#6d7378;
  --grey-band:#e6e7e8;
  --footer:#ededee;
  --white:#ffffff;
  --line:#d9dcdf;
}
*{box-sizing:border-box;margin:0;padding:0}
html,body{width:1200px;height:2556px;overflow:hidden}
body{font-family:'Lato',Arial,sans-serif;color:var(--ink);background:var(--white);position:relative}

/* hero */
.hero{position:absolute;left:0;top:0;width:1200px;height:620px;overflow:hidden}
.hero-photo{position:absolute;inset:0;background:linear-gradient(100deg,#3a4450 0%,#56606a 35%,#7c6f67 60%,#4a4f58 100%)}
.hero-shade{position:absolute;inset:0;background:rgba(20,28,38,.35)}
.nav{position:absolute;left:0;top:0;width:1200px;height:100px;display:flex;align-items:center;padding:0 120px}
.brand{display:flex;align-items:center;gap:12px;color:var(--white);font-size:34px;font-weight:700}
.brand-mark{width:30px;height:30px;border-radius:50%;background:var(--brand)}
.menu{margin-left:auto;display:flex;gap:56px;color:var(--white);font-size:18px;font-weight:700}
.start{position:absolute;left:0;top:330px;width:1200px;text-align:center}
.start h1{font-size:76px;font-weight:400;color:var(--white);letter-spacing:1px}
.signup{margin:38px auto 0;width:720px;height:58px;background:rgba(70,80,92,.75);border:1px solid rgba(255,255,255,.35);border-radius:30px;display:flex;align-items:center;padding:0 6px 0 30px}
.signup span{color:#dfe3e6;font-size:17px}
.submit{margin-left:auto;height:46px;width:150px;border-radius:24px;background:var(--brand);color:var(--white);font-size:18px;display:flex;align-items:center;justify-content:center}
.consent{margin:22px auto 0;width:720px;display:flex;align-items:center;gap:10px;color:var(--white);font-size:13px}
.consent i{width:15px;height:15px;background:var(--white);border-radius:2px;display:block}

/* stats */
.stats{position:absolute;left:0;top:620px;width:1200px;height:150px;display:flex;justify-content:center;padding-top:30px}
.stat{width:220px;text-align:center;border-right:1px solid var(--line)}
.stat:last-child{border-right:none}
.stat b{display:block;font-size:44px;font-weight:400;color:var(--brand)}
.stat small{display:block;margin-top:6px;font-size:11px;color:var(--muted);letter-spacing:.5px;line-height:1.35}

/* founder */
.founder{position:absolute;left:0;top:780px;width:1200px;height:380px;background:var(--grey-band)}
.founder-photo{position:absolute;left:220px;top:90px;width:200px;height:200px;border-radius:50%;border:6px solid var(--white);background:linear-gradient(160deg,#c9ced4,#7e8894 60%,#3f4a5a)}
.founder-text{position:absolute;left:470px;top:110px}
.founder-text h2{font-size:32px;font-weight:400;margin-bottom:26px}
.founder-text p{font-size:15px;color:#3d4246;line-height:1.75}

/* workflow */
.workflow{position:absolute;left:0;top:1160px;width:1200px;height:490px;background:linear-gradient(180deg,var(--brand-light),var(--brand))}
.workflow h2{position:absolute;top:60px;width:1200px;text-align:center;font-size:32px;font-weight:400;color:var(--white)}
.workflow .sub{position:absolute;top:110px;width:1200px;text-align:center;font-size:17px;color:#d6f0fb}
.phone{position:absolute;left:210px;top:160px;width:230px;height:330px;background:#f4f5f6;border-radius:28px 28px 0 0;padding:34px 12px 0}
.screen{background:var(--white);height:100%;padding:12px 10px;font-size:9px;color:var(--muted);line-height:1.9}
.screen .top{color:var(--brand);font-weight:700;font-size:9px;line-height:1.3;margin-bottom:10px}
.screen .bar{height:22px;background:var(--brand);margin:10px 0 8px}
.screen hr{border:none;border-top:1px solid var(--line)}
.features{position:absolute;left:560px;top:190px;width:440px}
.feature{display:flex;align-items:center;gap:26px;height:92px}
.feature-icon{width:56px;height:56px;flex:none;border-radius:50%;border:2px solid rgba(255,255,255,.8);display:flex;align-items:center;justify-content:center}
.feature p{font-size:14px;color:var(--white);line-height:1.5}

/* brands */
.brands{position:absolute;left:0;top:1650px;width:1200px;height:760px}
.brands h2{position:absolute;top:52px;width:1200px;text-align:center;font-size:36px;font-weight:400}
.brands .sub{position:absolute;top:104px;width:1200px;text-align:center;font-size:18px;color:var(--brand)}
.collage{position:absolute;left:460px;top:165px;width:300px;height:130px}
.shot{position:absolute;width:110px;height:90px;border:5px solid var(--white);box-shadow:0 3px 8px rgba(0,0,0,.25)}
.logo-grid{position:absolute;left:190px;top:320px;width:820px;height:420px;background:var(--white);display:grid;grid-template-columns:repeat(7,1fr);grid-template-rows:repeat(5,1fr);box-shadow:0 0 0 1px #f0f1f2}
.maker{display:flex;flex-direction:column;align-items:center;justify-content:center;gap:7px;font-size:12px;font-weight:700;color:#3a3f44}
.maker i{width:22px;height:22px;border-radius:50%;background:#9aa1a8;display:block}

/* footer */
.footer{position:absolute;left:0;top:2420px;width:1200px;height:136px;background:var(--footer);display:flex;align-items:center;justify-content:center;font-size:13px;color:var(--muted)}
</style>
</head>
<body>

<header class="hero">
  <div class="hero-photo" role="img" aria-label="Photo of a smiling shopper holding a tablet in a clothing store"></div>
  <div class="hero-shade"></div>
  <nav class="nav">
    <div class="brand"><span class="brand-mark"></span>Plumora88</div>
    <div class="menu"><span>About</span><span>Results</span><span>How</span><span>Free Trail</span></div>
  </nav>
  <div class="start">
    <h1>Start Here</h1>
    <div class="signup"><span>Your Email address</span><div class="submit">Submit</div></div>
    <div class="consent"><i></i>Yes, I have read and agree to the Privacy Policy and agree to receive email marketing from Plumora88</div>
  </div>
</header>

<section class="stats">
  <div class="stat"><b>2.2m</b><small>PHOTOS REVIEWED<br>LAST YEAR</small></div>
  <div class="stat"><b>5p</b><small>FROM PER PHOTO<br>REVIEWED</small></div>
  <div class="stat"><b>97.2%</b><small>AVERAGE<br>COMPLIANCE</small></div>
  <div class="stat"><b>3-8%</b><small>SALES<br>INCREASE</small></div>
</section>

<section class="founder">
  <div class="founder-photo" role="img" aria-label="Portrait photo of the company founder"></div>
  <div class="founder-text">
    <h2>Born Out of Retail Execution</h2>
    <p>Fonunder Daniel Ashworth 18 years of international retail experience<br>
    Vice President Supply Chain Northfield Stores Canada<br>
    Innovation Director - Brightline Merchandising UK</p>
  </div>
</section>

<section class="workflow">
  <h2>Increasing Sales with a Simple Photo &amp; Digital Workflow</h2>
  <div class="sub">+ 3-8% Sales with strict compliance</div>
  <div class="phone">
    <div class="screen">
      <div class="top">Store check submitted successfully<br>12-05-2016 10:24 AM</div>
      <hr>Store 214<hr>Aisle 6 promo<hr>Status: approved
      <div class="bar"></div>
      Next review in 2 days
    </div>
  </div>
  <div class="features">
    <div class="feature">
      <div class="feature-icon"><svg width="26" height="26" viewBox="0 0 26 26" fill="none" stroke="#fff" stroke-width="2"><circle cx="13" cy="13" r="10"/><path d="M13 7v6l4 3"/></svg></div>
      <p>In Minutes verify national promotions or range changes</p>
    </div>
    <div class="feature">
      <div class="feature-icon"><svg width="24" height="26" viewBox="0 0 24 26" fill="none" stroke="#fff" stroke-width="2"><path d="M12 24s8-8 8-14a8 8 0 0 0-16 0c0 6 8 14 8 14z"/><circle cx="12" cy="10" r="3"/></svg></div>
      <p>Real time insights why locations are not performing</p>
    </div>
    <div class="feature">
      <div class="feature-icon"><svg width="26" height="20" viewBox="0 0 26 20" fill="none" stroke="#fff" stroke-width="2"><rect x="1" y="1" width="24" height="18" rx="2"/><path d="M1 2l12 9 12-9"/></svg></div>
      <p>Eliminate field management audits, email, calls with a digital workflow</p>
    </div>
  </div>
</section>

<section class="brands">
  <h2>Serving Top Retailer and Brands</h2>
  <div class="sub">2.2 m Photo's verified per year</div>
  <div class="collage">
    <div class="shot" style="left:0;top:20px;transform:rotate(-8deg);background:linear-gradient(135deg,#c9a98e,#6e5a4d)" role="img" aria-label="Store shelf photo"></div>
    <div class="shot" style="left:95px;top:5px;transform:rotate(3deg);background:linear-gradient(135deg,#e3e6ea,#8f9aa6)" role="img" aria-label="Retail display photo"></div>
    <div class="shot" style="left:190px;top:22px;transform:rotate(9deg);background:linear-gradient(135deg,#b8c3cc,#56626e)" role="img" aria-label="Car showroom photo"></div>
  </div>
  <div class="logo-grid">
    <div class="maker"><i></i>Arvane</div><div class="maker"><i></i>Helmor</div><div class="maker"><i></i>Dalvo</div><div class="maker"><i></i>Hokari</div><div class="maker"><i></i>Mervale</div><div class="maker"><i></i>Landrix</div><div class="maker"><i></i>Jarrow</div>
    <div class="maker"><i></i>Acren</div><div class="maker"><i></i>Tovella</div><div class="maker"><i></i>Suvaro</div><div class="maker"><i></i>Chenwick</div><div class="maker"><i></i>Bavrin</div><div class="maker"><i></i>Volmar</div><div class="maker"><i></i>Mitara</div>
    <div class="maker"><i></i>Nisbo</div><div class="maker"><i></i>Lexor</div><div class="maker"><i></i>Infara</div><div class="maker"><i></i>Cherlan</div><div class="maker"><i></i>Aldor</div><div class="maker"><i></i>Minto</div><div class="maker"><i></i>Kelvo</div>
    <div class="maker"><i></i>Fordane</div><div class="maker"><i></i>Mazoro</div><div class="maker"><i></i>Valtor</div><div class="maker"><i></i>Citrane</div><div class="maker"><i></i>Renvik</div><div class="maker"><i></i>Skovel</div><div class="maker"><i></i>Ferrando</div>
    <div class="maker"><i></i>Subrin</div><div class="maker"><i></i>Jaxon</div><div class="maker"><i></i>Porvel</div><div class="maker"><i></i>Pelgard</div><div class="maker"><i></i>Orvel</div><div class="maker"><i></i>Fialo</div><div class="maker"><i></i>Alvaro</div>
  </div>
</section>

<footer class="footer">© 2016 Company Name. All right reserved. Terms of Use</footer>

</body>
</html>
```